Agriculture Business Card

I want to use my existing logo and use my tagline of "Test First...Then Plant" on the card. Looking for a double sided card that will really get peoples attention.
Contact Info:
Marlow Field Crop Edge
Calvin Brusk
2917 K Lane
Larkin, NE 68593
402-555-0193
calvin.r.brusk@fieldmailbox.net

```html
<!DOCTYPE html>
<html lang="en">
<head>
<meta charset="utf-8">
<title>Marlow Field Crop Edge – Business Card</title>
<link href="https://fonts.googleapis.com/css2?family=Fjalla+One&family=Arimo:wght@400;700&display=swap" rel="stylesheet">
<style>
  :root {
    --bg: #e9e9e9;
    --card: #333333;
    --white: #ffffff;
    --muted: #e6e6e6;
    --green: #3fae3a;
    --yellow: #f4b51f;
    --pattern-dark: #262626;
    --pattern-light: #7d7d7d;
  }
  * { box-sizing: border-box; margin: 0; padding: 0; }
  html, body { width: 1200px; height: 802px; overflow: hidden; }
  body {
    background: var(--bg);
    display: flex;
    align-items: center;
    justify-content: center;
    gap: 40px;
    font-family: "Arimo", Arial, sans-serif;
  }
  .card {
    position: relative;
    width: 540px;
    height: 309px;
    background: var(--card);
    overflow: hidden;
    box-shadow: 0 6px 18px rgba(0,0,0,.25);
  }

  .brand-name {
    font-family: "Fjalla One", "Arial Narrow", sans-serif;
    color: var(--white);
    font-size: 27px;
    line-height: 1.05;
    text-align: right;
  }
  .front .brand {
    position: absolute;
    right: 58px;
    top: 70px;
    display: flex;
    align-items: center;
    gap: 14px;
  }
  .brand-dot {
    width: 58px;
    height: 58px;
    border-radius: 50%;
    background: var(--yellow);
    flex: none;
  }
  .divider {
    position: absolute;
    left: 36px;
    right: 40px;
    top: 196px;
    height: 1px;
    background: var(--muted);
  }
  .holder-name {
    position: absolute;
    left: 36px;
    top: 162px;
    color: var(--green);
    font-weight: 700;
    font-size: 24px;
    letter-spacing: .5px;
    text-transform: uppercase;
  }
  .contact {
    position: absolute;
    left: 36px;
    top: 208px;
    list-style: none;
    color: var(--white);
    font-size: 15px;
    line-height: 22px;
  }
  .contact li { display: flex; align-items: center; gap: 8px; }
  .contact svg { width: 13px; height: 13px; flex: none; }
  .address {
    position: absolute;
    right: 40px;
    top: 208px;
    color: var(--white);
    font-size: 15px;
    line-height: 22px;
    font-style: normal;
  }

  .pattern {
    position: absolute;
    inset: 0;
    background: linear-gradient(160deg, var(--pattern-dark) 0%, var(--pattern-dark) 45%, var(--pattern-light) 100%);
  }
  .back .lockup {
    position: absolute;
    left: 130px;
    top: 118px;
    display: flex;
    align-items: center;
    gap: 14px;
  }
  .back .brand-name { text-align: center; font-size: 29px; }
  .tagline {
    display: block;
    margin-top: 6px;
    font-family: "Arimo", Arial, sans-serif;
    font-weight: 700;
    font-size: 16px;
    color: var(--yellow);
  }
</style>
</head>
<body>

  <section class="card front" aria-label="Card front">
    <div class="brand">
      <span class="brand-dot" aria-hidden="true"></span>
      <div class="brand-name">Marlow Field<br>Crop Edge</div>
    </div>

    <h1 class="holder-name">Calvin Brusk</h1>
    <div class="divider"></div>

    <ul class="contact">
      <li>
        <svg viewBox="0 0 16 16" aria-hidden="true"><circle cx="8" cy="8" r="8" fill="var(--green)"/><path d="M5 4.5c.6-.4 1.2-.2 1.5.4l.6 1.2c.2.4 0 .8-.3 1l-.5.4c.4.9 1.1 1.6 2 2l.4-.5c.2-.3.6-.5 1-.3l1.2.6c.6.3.8.9.4 1.5-.6.9-1.7 1-2.7.5C6.7 10.4 5.6 9.3 4.8 7.5c-.5-1-.4-2.2.2-3z" fill="var(--card)"/></svg>
        402-555-0193
      </li>
      <li>
        <svg viewBox="0 0 16 16" aria-hidden="true"><rect x="1" y="3" width="14" height="10" rx="1" fill="var(--green)"/><path d="M1.5 3.8 8 9l6.5-5.2" fill="none" stroke="var(--card)" stroke-width="1.3"/></svg>
        calvin.r.brusk@fieldmailbox.net
      </li>
    </ul>

    <address class="address">2917 K Lane<br>Larkin, NE 68593</address>
  </section>

  <section class="card back" aria-label="Card back">
    <div class="pattern" role="img" aria-label="Repeating embossed pattern of the company emblem across the card"></div>
    <div class="lockup">
      <span class="brand-dot" aria-hidden="true"></span>
      <div class="brand-name">Marlow Field<br>Crop Edge
        <span class="tagline">Test First...Then Plant</span>
      </div>
    </div>
  </section>

</body>
</html>
```